Business Card for Professional Photographer

I'm looking for an eye catching modern clean design that compliments my logo/ website fonts & colours.
I specialise in architecture, corporate & commercial photography so I'm marketing to professional clients rather than portrait / wedding clients.

I would prefer to not have a solid black design.

My logo brand guide is as follows :

Main front font. : Reislust
Main font colour : #fff
Slogan front font : Ubuntu Bold
Monogram front font : Venti Medium
Container colour : #fff

I need print ready files in pdf .png & .eps formats.

Included in the files below are some screen grabs as reference to font & colours etc.

```html
<!DOCTYPE html>
<html lang="en">
<head>
<meta charset="utf-8">
<title>Still Meridian – Business Card</title>
<link rel="stylesheet" href="https://fonts.googleapis.com/css2?family=Source+Sans+3:wght@400;600&display=swap">
<style>
  :root {
    --backdrop: #1e1e1f;
    --card: #eff0f3;
    --gold: #b98f4f;
    --ink: #5a5a5c;
  }
  * { margin: 0; padding: 0; box-sizing: border-box; }
  html, body { width: 1200px; height: 900px; overflow: hidden; background: var(--backdrop); }
  .canvas { position: relative; width: 1200px; height: 900px; font-family: "Source Sans 3", sans-serif; }
  .card-shapes { position: absolute; inset: 0; }
  .card-shape { fill: var(--card); }

  .brand { position: absolute; display: flex; align-items: center; color: var(--gold); font-weight: 400; text-transform: uppercase; white-space: nowrap; }
  .brand-dot { border-radius: 50%; background: var(--gold); flex: none; }
  .brand--small { left: 190px; top: 345px; font-size: 12.5px; letter-spacing: 2.6px; gap: 9px; }
  .brand--small .brand-dot { width: 10px; height: 10px; }
  .brand--large { left: 700px; top: 418px; font-size: 21px; letter-spacing: 4.6px; gap: 16px; }
  .brand--large .brand-dot { width: 18px; height: 18px; }

  .person { position: absolute; left: 190px; top: 418px; }
  .person-name { font-size: 18px; font-weight: 600; color: var(--gold); line-height: 1.2; }
  .person-role { font-size: 14.5px; color: var(--ink); line-height: 1.4; }
  .divider { width: 17px; height: 1px; background: var(--gold); margin-top: 13px; }

  .contact-list { position: absolute; left: 190px; top: 488px; list-style: none; }
  .contact-item { display: flex; align-items: center; gap: 8px; height: 21.3px; font-size: 14px; color: var(--ink); }
  .contact-icon { width: 9px; height: 9px; fill: var(--gold); flex: none; }
</style>
</head>
<body>
<div class="canvas">
  <svg class="card-shapes" width="1200" height="900" viewBox="0 0 1200 900" aria-hidden="true">
    <path class="card-shape card-shape--back" d="M145,338 Q145,278 205,278 L243,278 L248,258 Q257,224 292,224 L452,224 Q487,224 496,258 L502,278 L540,278 Q600,278 600,338 L600,548 Q600,608 540,608 L205,608 Q145,608 145,548 Z"/>
    <path class="card-shape card-shape--front" d="M610,344 Q610,284 670,284 L703,284 L708,264 Q717,233 752,233 L902,233 Q937,233 946,264 L951,284 L985,284 Q1045,284 1045,344 L1045,540 Q1045,600 985,600 L670,600 Q610,600 610,540 Z"/>
  </svg>

  <div class="brand brand--small"><span class="brand-dot"></span>Still Meridian</div>

  <div class="person">
    <p class="person-name">Dara Lindqvist</p>
    <p class="person-role">Manager</p>
    <div class="divider"></div>
  </div>

  <ul class="contact-list">
    <li class="contact-item">
      <svg class="contact-icon" viewBox="0 0 10 10"><path d="M2 0.5 L3.6 0.5 L4.2 2.8 L3.2 3.6 Q4.2 5.8 6.4 6.8 L7.2 5.8 L9.5 6.4 L9.5 8 Q9.5 9.5 8 9.5 Q0.5 9 0.5 2 Q0.5 0.5 2 0.5 Z"/></svg>
      555-018-2294
    </li>
    <li class="contact-item">
      <svg class="contact-icon" viewBox="0 0 10 10"><path d="M0 1.5 H10 V8.5 H0 Z M1 2.5 L5 5.5 L9 2.5 Z" fill-rule="evenodd"/></svg>
      info@northlightframes.com
    </li>
    <li class="contact-item">
      <svg class="contact-icon" viewBox="0 0 10 10"><circle cx="5" cy="5" r="4.6" fill="none" stroke="#b98f4f" stroke-width="1"/><path d="M0.5 5 H9.5 M5 0.5 Q2 5 5 9.5 M5 0.5 Q8 5 5 9.5" fill="none" stroke="#b98f4f" stroke-width="0.8"/></svg>
      www.northlightframes.com
    </li>
  </ul>

  <div class="brand brand--large"><span class="brand-dot"></span>Still Meridian</div>
</div>
</body>
</html>
```